Webdesign für Brenner Flusskraft
Zielgruppe
Ansprechpartner für Planung und Errichtung von Stromerzeugung durch erneuerbare Energien. Alle Interessen im privaten, teilöffentlichen und öffentlichen Bereich, die mittel- und langfristig umweltschonenden Strom nutzen wollen.
Aufgabenstellung
- Farben bitte in den Unternehmensfarben Blau/Weiß mit einem kleinen Anteil Orange
- Bilder nach Möglichkeit bitte nur eigene (siehe Anhang)
- klare und übersichtliche Struktur
- KEIN Abklatsch der alten Webseite

```html
<!DOCTYPE html>
<html lang="de">
<head>
<meta charset="utf-8">
<title>Brenner Flusskraft – Über uns</title>
<link href="https://fonts.googleapis.com/css2?family=Poppins:wght@500;600;700&family=Roboto:wght@300;400&family=Roboto+Condensed:wght@400&display=swap" rel="stylesheet">
<style>
:root{
  --navy:#14148a;
  --orange:#ff8a00;
  --sky:#7eaefa;
  --text:#2b2b3a;
  --bar:#f4f4f4;
  --white:#ffffff;
}
*{margin:0;padding:0;box-sizing:border-box}
html,body{width:1200px;height:579px;overflow:hidden;background:var(--white)}
body{position:relative;font-family:'Roboto',sans-serif;color:var(--text)}
.topbar{position:absolute;left:0;top:0;width:1200px;height:26px;background:var(--bar);border-bottom:1px solid var(--navy);font-family:'Poppins',sans-serif;color:var(--navy)}
.topbar .mail-icon{position:absolute;left:223px;top:10px}
.topbar .mail{position:absolute;left:252px;top:7px;font-size:9px;font-weight:500}
.topbar .claim{position:absolute;left:501px;top:10px;font-size:9.5px;font-weight:500}
.topbar .pin-icon{position:absolute;left:821px;top:7px}
.topbar .address{position:absolute;left:851px;top:3px;font-size:9.5px;font-weight:500;line-height:11px}
.topbar .address small{display:block;font-family:'Roboto Condensed',sans-serif;font-size:8.5px;font-weight:400}
.photo-team{position:absolute;left:257px;top:66px;width:319px;height:312px;background:linear-gradient(135deg,#1f3324 0%,#2c4a30 30%,#6c9fd0 60%,#9cc3e6 80%,#24372a 100%)}
.photo-tail{position:absolute;left:512px;top:377px;width:64px;height:110px;background:linear-gradient(180deg,#2a3b4e,#1b2a22)}
.photo-frame{position:absolute;left:257px;top:378px;width:255px;height:170px;background:var(--white)}
.photo-model{position:absolute;left:270px;top:391px;width:230px;height:147px;background:linear-gradient(160deg,#d8d8dc 0%,#f2efe8 35%,#5f8c3e 60%,#3f6b2a 80%,#6a5a3c 100%)}
.badge{position:absolute;left:213px;top:104px;width:92px;height:92px;border-radius:50%;background:var(--orange);color:var(--white);text-align:center;font-family:'Poppins',sans-serif;font-weight:600;font-size:9px;line-height:17px}
.badge svg{display:block;margin:12px auto 4px}
.content{position:absolute;left:613px;top:66px;width:320px}
.eyebrow{font-family:'Poppins',sans-serif;font-size:8.6px;font-weight:600;letter-spacing:1.4px;color:var(--orange);line-height:10px;padding-top:1px}
.eyebrow-line{width:108px;height:1.5px;background:var(--orange);margin-top:7px}
h1{margin-top:16px;font-family:'Poppins',sans-serif;font-size:19.5px;font-weight:700;line-height:23px;color:var(--navy)}
.intro{margin-top:14px;font-size:8.9px;font-weight:300;line-height:17px;color:#1e1e2a}
.intro+.intro{margin-top:9px}
.signature{position:absolute;left:613px;top:356px;width:234px;height:22px;background:linear-gradient(90deg,rgba(20,20,138,.85),rgba(20,20,138,.6));border-radius:3px}
.cta{position:absolute;left:613px;top:406px;width:319px;height:93px;display:flex}
.cta .icon{width:95px;background:var(--orange);display:flex;align-items:center;justify-content:center}
.cta .info{flex:1;background:var(--sky);padding-left:15px;padding-top:25px;font-family:'Poppins',sans-serif;color:var(--navy)}
.cta .label{font-size:11px;font-weight:700;letter-spacing:2px}
.cta .phone{margin-top:2px;font-size:19.5px;font-weight:700;letter-spacing:1.5px}
</style>
</head>
<body>
<header class="topbar">
  <svg class="mail-icon" width="12" height="9" viewBox="0 0 12 9"><rect width="12" height="9" rx="1" fill="#14148a"/><path d="M0.5 1 6 5 11.5 1" stroke="#f4f4f4" stroke-width="1" fill="none"/></svg>
  <span class="mail">info@brenner-flusskraft.de</span>
  <span class="claim">IHR PROFI FÜR ERNEUERBARE ENERGIEN</span>
  <svg class="pin-icon" width="12" height="15" viewBox="0 0 12 15"><path d="M6 0C2.7 0 0 2.6 0 5.9 0 10 6 15 6 15s6-5 6-9.1C12 2.6 9.3 0 6 0z" fill="#14148a"/><circle cx="6" cy="5.8" r="2.2" fill="#f4f4f4"/></svg>
  <div class="address">Ahornweg 14<small>09123 Musterau</small></div>
</header>

<div class="photo-team" role="img" aria-label="Foto: zwei Inhaber in hellblauen Hemden vor grünem Hintergrund"></div>
<div class="photo-tail" role="img" aria-label="Fortsetzung des Teamfotos"></div>
<div class="photo-frame"></div>
<div class="photo-model" role="img" aria-label="Foto: Modell mit Windrädern auf Rasenfläche bei der Planung"></div>

<div class="badge">
  <svg width="30" height="28" viewBox="0 0 24 23"><path d="M12 1.5l3.1 6.6 7.1.8-5.3 4.9 1.5 7.1L12 17.3 5.6 20.9l1.5-7.1L1.8 8.9l7.1-.8z" fill="none" stroke="#fff" stroke-width="1.3" stroke-linejoin="round"/></svg>
  Über 30 Jahre<br>Erfahrung
</div>

<section class="content">
  <p class="eyebrow">Ihr Partner für nachhaltige Stromerzeugung in privaten, teilöffentlichen und öffentlichen Bereichen.</p>
  <div class="eyebrow-line"></div>
  <h1>Brenner Flusskraft:<br>Pioniere in Erneuerbarer Energie</h1>
  <p class="intro">Mit über 30 Jahren Erfahrung in der Planung und Errichtung von erneuerbare Energien Anlagen sind wir Ihre Ansprechpartner wenn es um die Stromerzeugung und Sektor Kopplung geht. Durch unsere große Erfahrung im Bereich des Energiebaus und der erneuerbaren Energien haben Sie mit uns ein leistungsfähiges Unternehmen für Ihre Projekte an der Hand. Sprechen Sie uns einfach für Ihre Projekte an, wir stehen von der Ingenieurplanung, über die Ausführung, bis hin zur Betriebsführung an Ihrer Seite.</p>
  <p class="intro">Als Familienunternehmen in zweiter Generation finden Sie bei uns kurze Wege, hohe qualitative Leistungen und einen großenErfahrungsschatz.</p>
</section>

<div class="signature" role="img" aria-label="Handschriftlicher Gruß: Herzlichst Ihre Familie Brenner"></div>

<div class="cta">
  <div class="icon">
    <svg width="42" height="40" viewBox="0 0 24 23"><path d="M12 1.5l3.1 6.6 7.1.8-5.3 4.9 1.5 7.1L12 17.3 5.6 20.9l1.5-7.1L1.8 8.9l7.1-.8z" fill="none" stroke="#fff" stroke-width="1.5" stroke-linejoin="round"/></svg>
  </div>
  <div class="info">
    <div class="label">JETZT BERATEN LASSEN</div>
    <div class="phone">0800 987 65 43</div>
  </div>
</div>
</body>
</html>
```